Wix Design for a Clothing Design Web Marketing Site

We need a Wix design and content (including any images and copy) for a clothing design web storefront, Sew To Suit (or sewtosuit). Rough ideas and content can be found at http://marenvoltis.wix.com/sewtosuit.

Sew To Suit is an innovative business concept that combines fashion and entertainment. The business model allows customers to actively participate in the creation of fashion designs/concepts , visualize the garment in the customer’s body in 3D, and buy the physical garment made specially to fit the customer.
The fashion consultant will be able to create the design based on client's desires and test various possibilities (size, fabric, cut, etc..) in front of the customer, using software Drapova (the software is a key component of this business model)
(when developing the website use images from Drapova)
After the design is created, the customer can choose to order the actual piece. The garment will be made according to the created design, the customer measurements.

Target Market(s)

Primarily women from 25 to 45, who are fashion enthusiasts and appreciate fit and exclusivity. They are hedonistic shoppers, who shop for entertainment.
Men (metrosexuals) who are fashion enthusiasts, also hedonistic shoppers.

Industry/Entity Type

Clothing

Font styles to use
Serif
Sans Serif

Requirements
Must have
• Must have a landing page (home) or section, that gives the consumer an idea of what Sew To Suit will do for them, an about page or section that tells about the company and product, a how it works page or section that describes how it works (http://marenvoltis.wix.com/sewtosuit#!services3/c192y), and page or section about pricing, and a page or section on how to contact us.
Nice to have
• Very modern and clean. The website must be based on the main picture of the studio in the example. If that studio is the store, what will the website look like?
• Colors yellow, grey and white. Use the zig zag in yellow and white. You can change the size of the lines. The zig zagi gives the modern and bold accent. Outfits in pictures must show nicely tailored garments.

```html
<!DOCTYPE html>
<html lang="en">
<head>
<meta charset="utf-8">
<title>Sew To Suit</title>
<link href="https://fonts.googleapis.com/css2?family=Lora:ital,wght@0,400;0,700;1,400&display=swap" rel="stylesheet">
<style>
  :root{
    --black:#000;
    --white:#fff;
    --yellow:#d9dd1e;
    --nav-yellow:#eef03a;
    --ink:#3a3a3a;
    --ink-soft:#555;
    --sepia-light:#d8c3ad;
    --sepia-mid:#a98a6e;
    --sepia-dark:#5a4330;
    --rule:#222;
  }
  *{margin:0;padding:0;box-sizing:border-box}
  html,body{width:965px;height:1200px;overflow:hidden;background:var(--black)}
  body{font-family:"Lora",serif;color:var(--white);position:relative}
  .abs{position:absolute}

  /* header */
  .site-header{left:0;top:0;width:965px;height:195px;background:var(--black)}
  .brand-frame{left:414px;top:17px;width:137px;height:109px;border:1px solid #bbb;display:flex;align-items:center;justify-content:center}
  .brand-box{width:117px;height:87px;background:var(--yellow);display:flex;align-items:center;justify-content:center}
  .brand-name{font-family:"Lora",serif;font-weight:700;font-size:13px;color:var(--black)}
  .main-nav{left:0;top:152px;width:965px;display:flex;justify-content:center;font-size:11px;letter-spacing:.2px}
  .main-nav a{color:var(--white);text-decoration:none;padding:0 14px;border-left:1px solid #ccc;line-height:18px}
  .main-nav a:first-child{border-left:none}
  .main-nav a.active{color:var(--nav-yellow)}

  /* photos */
  .photo{background:linear-gradient(135deg,var(--sepia-light),var(--sepia-mid) 55%,var(--sepia-dark))}

  /* hero */
  .hero-photo-left{left:0;top:195px;width:482px;height:318px}
  .hero-photo-right{left:794px;top:195px;width:171px;height:318px;background:linear-gradient(160deg,var(--sepia-dark),var(--sepia-mid) 60%,var(--sepia-light))}
  .hero-panel{left:482px;top:195px;width:312px;height:318px;background:var(--white);color:var(--ink)}
  .hero-notch{left:447px;top:333px}
  .hero-kicker{left:37px;top:46px;font-size:38px;font-weight:400;color:#4a4a4a;line-height:1}
  .hero-title{left:37px;top:92px;font-size:44px;font-weight:700;color:#444;line-height:1;white-space:nowrap}
  .hero-title .accent{color:var(--yellow)}
  .hero-lede{left:37px;top:165px;width:270px;font-style:italic;font-size:17px;line-height:27px;color:#555}
  .btn-read{left:37px;top:248px;width:130px;height:35px;background:var(--black);border:1px solid var(--yellow);color:var(--nav-yellow);font-size:13px;font-weight:700;display:flex;align-items:center;justify-content:center;gap:4px}

  /* steps */
  .steps-photo-left{left:0;top:513px;width:116px;height:489px;background:linear-gradient(180deg,var(--sepia-light),var(--sepia-mid) 70%,var(--sepia-light))}
  .steps-panel{left:116px;top:513px;width:366px;height:489px;background:var(--white);color:var(--ink)}
  .steps-photo-right{left:482px;top:513px;width:483px;height:489px}
  .steps-notch{left:482px;top:713px}
  .step-list{left:43px;top:32px;width:300px;list-style:none}
  .step{margin-bottom:10px}
  .step h2{font-size:18px;font-weight:700;color:#333;line-height:24px}
  .step p{font-size:10.5px;line-height:23px;color:#333}

  /* footer */
  .site-footer{left:0;top:1002px;width:965px;height:198px;background:var(--black)}
  .zig-edge{left:0;width:965px;height:4px}
  .footer-brand{left:79px;top:27px;width:123px;height:92px;background:var(--yellow);display:flex;align-items:center;justify-content:center}
  .footer-nav{left:222px;top:70px;display:flex;font-size:11px}
  .footer-nav a{color:var(--white);text-decoration:none;padding:0 11px;border-left:1px solid #ccc;line-height:14px}
  .footer-nav a:first-child{border-left:none;padding-left:0}
  .contact-list{right:79px;top:43px;list-style:none;font-size:11px;text-align:right}
  .contact-list li{display:flex;justify-content:flex-end;align-items:center;gap:7px;height:21.5px}
  .contact-list svg{fill:var(--nav-yellow)}
  .footer-rule{left:0;top:149px;width:965px;height:1px;background:var(--rule)}
  .copyright{left:0;top:165px;width:965px;text-align:center;font-size:11px}
  .social{left:807px;top:169px;display:flex;gap:9px}
  .social span{width:14px;height:14px;border-radius:50%;background:var(--white);display:block}
</style>
</head>
<body>

<header class="site-header abs">
  <div class="brand-frame abs">
    <div class="brand-box"><span class="brand-name">Sew To Suit</span></div>
  </div>
  <nav class="main-nav abs">
    <a class="active" href="#">HOME</a>
    <a href="#">WHAT IS SEW TO SUIT?</a>
    <a href="#">HOW IS WORKS</a>
    <a href="#">PRICE</a>
    <a href="#">CONTACT US</a>
  </nav>
</header>

<section class="hero">
  <div class="hero-photo-left photo abs" role="img" aria-label="Sepia fashion photo of a woman and a man in tailored outfits among leaves"></div>
  <svg class="hero-notch abs" width="36" height="38" viewBox="0 0 36 38"><polygon points="36,0 0,19 36,38" fill="#fff"/></svg>
  <div class="hero-panel abs">
    <p class="hero-kicker abs">Welcome to</p>
    <h1 class="hero-title abs">Sew <span class="accent">To</span> Suit</h1>
    <p class="hero-lede abs">Clothes made specially for you and designed by you.</p>
    <a class="btn-read abs">READ MORE
      <svg width="9" height="9" viewBox="0 0 9 9"><path d="M1 1l3 3.5L1 8M5 1l3 3.5L5 8" stroke="#eef03a" stroke-width="1.6" fill="none"/></svg>
    </a>
  </div>
  <div class="hero-photo-right abs" role="img" aria-label="Sepia fashion photo detail with leaves and a seated model"></div>
</section>

<section class="steps">
  <div class="steps-photo-left abs" role="img" aria-label="Sepia photo of leaf shadows on a studio wall"></div>
  <div class="steps-panel abs">
    <ul class="step-list abs">
      <li class="step"><h2>Be Inspired</h2><p>Be inspired by the latest trends, iconic styles from all eras<br>and the most prestigious fashion shows</p></li>
      <li class="step"><h2>Design</h2><p>Learn about our unique process,&nbsp; where you<br>become the designer</p></li>
      <li class="step"><h2>Choose the Fabric</h2><p>First rate fabrics &amp; highest<br>quality materials</p></li>
      <li class="step"><h2>See your Creation</h2><p>See your creation in 3D</p></li>
      <li class="step"><h2>Wear it</h2><p>Wear your design, fitted for your exact body<br>measurements</p></li>
      <li class="step"><h2>Have Fun, Be Creative</h2><p>The thrilling experience of creating</p></li>
    </ul>
  </div>
  <div class="steps-photo-right photo abs" role="img" aria-label="Sepia fashion photo of a woman in sunglasses and a man in a patterned shirt"></div>
  <svg class="steps-notch abs" width="37" height="38" viewBox="0 0 37 38"><polygon points="0,0 37,19 0,38" fill="#fff"/></svg>
</section>

<footer class="site-footer abs">
  <div class="footer-brand abs"><span class="brand-name">Sew To Suit</span></div>
  <nav class="footer-nav abs">
    <a href="#">HOME</a>
    <a href="#">WHAT IS SEW TO SUIT?</a>
    <a href="#">MORE</a>
  </nav>
  <ul class="contact-list abs">
    <li><svg width="9" height="12" viewBox="0 0 9 12"><path d="M4.5 0A4.5 4.5 0 0 0 0 4.5C0 8 4.5 12 4.5 12S9 8 9 4.5A4.5 4.5 0 0 0 4.5 0zm0 6.3a1.8 1.8 0 1 1 0-3.6 1.8 1.8 0 0 1 0 3.6z"/></svg>Riverside, CA</li>
    <li><svg width="12" height="12" viewBox="0 0 12 12"><path d="M2.4 0l2 2.8-1.2 1.6c.8 1.8 2.2 3.2 4 4l1.6-1.2L12 9.2 10.6 12C4.8 11.6.4 7.2 0 1.4z"/></svg>1-555-014-2290</li>
    <li><svg width="15" height="11" viewBox="0 0 15 11"><path d="M0 0h15v1.5L7.5 6 0 1.5zM0 3.3l7.5 4.5L15 3.3V11H0z"/></svg>hello@sewtosuit.example</li>
  </ul>
  <div class="footer-rule abs"></div>
  <p class="copyright abs">@ 2015 Sew To Suit . All rights are reserved.</p>
  <div class="social abs" aria-label="Social links"><span></span><span></span><span></span><span></span></div>
</footer>

</body>
</html>
```